Updated Business Card Re-design (Logo Provided)

I am needing to update our business cards for our practice, Brightfield Care Partners. We are a personal injury and wellness practice. The final design should be elegant and classy, but a type of card people would want to keep. Any samples should only have Dr. Tomas Verlinde on the template.
Updates

Went on vacation/holiday

Need extra days to review

Target Market(s)

Personal Injury clients, wellness clients

Industry/Entity Type

Personal Injury, medical, wellness

Contact Information for Business Card

dr and practice name, offerings

Requirements
Must have
• Single sided, this will be printed on a transparent business card, no exceptions.

```html
<!DOCTYPE html>
<html lang="en">
<head>
<meta charset="utf-8">
<title>Brightfield Care Partners – Business Card</title>
<link rel="stylesheet" href="https://fonts.googleapis.com/css2?family=Fira+Sans+Condensed:wght@600&family=Roboto:wght@400;500&display=swap">
<style>
  :root{
    --page-bg:#e9edf2;
    --card-top:#2a2b2f;
    --card-bottom:#050506;
    --brand-blue:#2f6fb8;
    --brand-orange:#e0892f;
    --brand-green:#2f7d4c;
    --icon-green:#3f8e5b;
    --text-light:#c9cacf;
  }
  *{margin:0;padding:0;box-sizing:border-box}
  html,body{width:1200px;height:900px;overflow:hidden;background:var(--page-bg)}
  .card{
    position:absolute;left:151px;top:193px;width:898px;height:514px;
    border-radius:22px;overflow:hidden;
    background:linear-gradient(160deg,var(--card-top) 0%,#111214 45%,var(--card-bottom) 100%);
    box-shadow:0 18px 40px rgba(20,30,50,.25);
    font-family:"Roboto",sans-serif;
  }
  .practice-name{position:absolute;left:46px;top:20px;color:var(--brand-blue);
    font-family:"Fira Sans Condensed",sans-serif;font-weight:600;line-height:1}
  .practice-name .line-main{display:block;font-size:60px;letter-spacing:-1.5px;text-transform:uppercase}
  .practice-name .line-sub{display:block;font-size:40px;margin:8px 0 0 150px;text-transform:uppercase}
  .accent-bar{position:absolute;left:0;top:164px;width:12px;height:66px;background:var(--brand-orange)}
  .doctor-name{position:absolute;left:46px;top:166px;font-size:32px;font-weight:500;color:var(--brand-blue)}
  .offerings{position:absolute;left:46px;top:216px;font-size:22px;color:var(--brand-orange)}
  .contact-list{position:absolute;left:44px;top:262px;list-style:none}
  .contact-list li{display:flex;align-items:flex-start;height:39px;font-size:22px;color:var(--text-light);line-height:30px}
  .contact-list svg{width:22px;height:22px;margin:4px 16px 0 0;flex:none;fill:var(--icon-green)}
  .contact-list .address{height:auto;line-height:30px}
  .brand-mark{position:absolute;left:548px;top:382px;display:flex;align-items:center;gap:14px}
  .brand-mark .dot{width:40px;height:40px;border-radius:50%;background:var(--brand-orange)}
  .brand-mark .word{font-family:"Roboto",sans-serif;font-weight:500;font-size:52px;color:var(--brand-orange);line-height:1}
  .color-strip{position:absolute;bottom:0;height:16px}
  .strip-blue{left:180px;width:118px;background:var(--brand-blue)}
  .strip-orange{left:298px;width:296px;background:var(--brand-orange)}
  .strip-green{left:594px;width:304px;background:var(--brand-green)}
</style>
</head>
<body>
<div class="card">
  <h1 class="practice-name"><span class="line-main">Brightfield Care</span><span class="line-sub">Partners</span></h1>
  <div class="accent-bar"></div>
  <h2 class="doctor-name">Dr. Tomas Verlinde, D.C</h2>
  <p class="offerings">Medical-PT-Chiropractic</p>
  <ul class="contact-list">
    <li><svg viewBox="0 0 24 24"><path d="M6.6 10.8a15 15 0 0 0 6.6 6.6l2.2-2.2c.3-.3.7-.4 1-.2 1.1.4 2.3.6 3.6.6.6 0 1 .4 1 1V20c0 .6-.4 1-1 1A17 17 0 0 1 3 4c0-.6.4-1 1-1h3.5c.6 0 1 .4 1 1 0 1.3.2 2.5.6 3.6.1.3 0 .7-.2 1z"/></svg>555.214.7730</li>
    <li><svg viewBox="0 0 24 24"><path d="M7 1h10a2 2 0 0 1 2 2v18a2 2 0 0 1-2 2H7a2 2 0 0 1-2-2V3a2 2 0 0 1 2-2zm0 3v14h10V4zm5 15.5a1 1 0 1 0 0 2 1 1 0 0 0 0-2z"/></svg>555.483.1062</li>
    <li><svg viewBox="0 0 24 24"><path d="M3 5h18a1 1 0 0 1 1 1v12a1 1 0 0 1-1 1H3a1 1 0 0 1-1-1V6a1 1 0 0 1 1-1zm1 2.5V17h16V7.5l-8 5z M4.5 7l7.5 4.6L19.5 7z"/></svg>info@brightfieldcare.com</li>
    <li><svg viewBox="0 0 24 24"><path d="M12 2a10 10 0 1 0 0 20 10 10 0 0 0 0-20zm6.9 6h-3a15 15 0 0 0-1.3-3.9A8 8 0 0 1 18.9 8zM12 4c.8 1.2 1.5 2.5 1.9 4h-3.8c.4-1.5 1.1-2.8 1.9-4zM4.3 14a8 8 0 0 1 0-4h3.4a16 16 0 0 0 0 4zm.8 2h3a15 15 0 0 0 1.3 3.9A8 8 0 0 1 5.1 16zm3-8h-3a8 8 0 0 1 4.3-3.9A15 15 0 0 0 8.1 8zM12 20c-.8-1.2-1.5-2.5-1.9-4h3.8c-.4 1.5-1.1 2.8-1.9 4zm2.3-6H9.7a14 14 0 0 1 0-4h4.6a14 14 0 0 1 0 4zm.3 5.9a15 15 0 0 0 1.3-3.9h3a8 8 0 0 1-4.3 3.9zm1.7-5.9a16 16 0 0 0 0-4h3.4a8 8 0 0 1 0 4z"/></svg>brightfieldcare.com</li>
    <li class="address"><svg viewBox="0 0 24 24"><path d="M12 2a7 7 0 0 0-7 7c0 5.2 7 13 7 13s7-7.8 7-13a7 7 0 0 0-7-7zm0 9.5a2.5 2.5 0 1 1 0-5 2.5 2.5 0 0 1 0 5z"/></svg><span>2480 Meadow Ridge Rd, Suite 12<br>Fairhaven, GA 30555</span></li>
  </ul>
  <div class="brand-mark"><span class="dot"></span><span class="word">Brightfield</span></div>
  <div class="color-strip strip-blue"></div>
  <div class="color-strip strip-orange"></div>
  <div class="color-strip strip-green"></div>
</div>
</body>
</html>
```